Telecommunications/Power civil contractor needs business card design

Were a new telecommunications/power underground civil contractor that is looking for a new business card design. Our company colours are silver or grey and orange. Feel free to use the white background logo or the black background logo.

Target Market(s)

Local contractors, utility companies, private sector mining/energy companies, developers.

Industry/Entity Type

Telecommunications

Contact Information for Business Card

Each card will need the following info:
Persons name:
Title:
E-mail:
Phone number:
Shop Address:
Mailing Address:

Requirements
Must have
• Each card will need the following info:
• Persons name:
• Title:
• E-mail:
• Phone number:
• Shop Address:
• Mailing Address:

```html
<!DOCTYPE html>
<html lang="en">
<head>
<meta charset="utf-8">
<title>Tread Line Civil Inc – Business Card</title>
<link rel="stylesheet" href="https://fonts.googleapis.com/css2?family=Open+Sans:wght@400;600;700;800&display=swap">
<style>
  :root {
    --stage: #2b2d31;
    --card-white: #ffffff;
    --brand-orange: #f15a24;
    --brand-grey: #6d6e71;
    --text-light: #ffffff;
  }
  * { box-sizing: border-box; margin: 0; padding: 0; }
  html, body {
    width: 1200px; height: 864px; overflow: hidden;
    background: var(--stage);
    font-family: "Open Sans", Arial, sans-serif;
  }
  .stage { position: relative; width: 1200px; height: 864px; }
  .card {
    position: absolute; left: 320px; width: 560px; height: 320px;
    background: var(--card-white); overflow: hidden;
    box-shadow: 0 12px 30px rgba(0,0,0,.45);
  }
  .card--front { top: 60px; }
  .card--back { top: 468px; }

  /* Front */
  .front-brand {
    position: absolute; inset: 0;
    display: flex; flex-direction: column; align-items: center; justify-content: center;
  }
  .brand-dot {
    width: 96px; height: 96px; border-radius: 50%;
    background: var(--brand-orange); margin-bottom: 22px;
  }
  .brand-name {
    color: var(--brand-orange); font-weight: 800; text-align: center;
    text-transform: uppercase; line-height: 1.05;
  }
  .front-brand .brand-name { font-size: 38px; letter-spacing: 1px; }
  .front-brand .brand-name span { display: block; font-size: 24px; letter-spacing: 2px; }

  /* Back */
  .back-panel { position: absolute; inset: 0; }
  .contact {
    position: absolute; left: 30px; top: 28px; width: 270px;
    color: var(--text-light); font-size: 13.5px; line-height: 1.25;
  }
  .contact__name { font-size: 18px; font-weight: 700; }
  .contact__title { font-size: 12.5px; margin-bottom: 18px; }
  .contact__label { font-size: 15px; font-weight: 700; }
  .contact__block { margin-bottom: 14px; }
  .contact__line { display: flex; align-items: center; gap: 10px; margin-top: 6px; font-size: 14px; }
  .contact__line svg { width: 12px; height: 12px; flex: none; }
  .back-brand {
    position: absolute; left: 330px; top: 0; width: 210px; height: 320px;
    display: flex; flex-direction: column; align-items: center; justify-content: center;
  }
  .back-brand .brand-dot { width: 110px; height: 110px; margin-bottom: 18px; }
  .back-brand .brand-name { font-size: 22px; }
</style>
</head>
<body>
<main class="stage">
  <section class="card card--front" aria-label="Card front">
    <div class="front-brand">
      <div class="brand-dot"></div>
      <p class="brand-name">Tread Line<span>Civil Inc</span></p>
    </div>
  </section>

  <section class="card card--back" aria-label="Card back">
    <svg class="back-panel" viewBox="0 0 560 320" aria-hidden="true">
      <path d="M0 0 H360 C270 50 250 200 330 320 H0 Z" fill="var(--brand-orange)"/>
    </svg>
    <div class="contact">
      <p class="contact__name">Marcus Hale</p>
      <p class="contact__title">Managing Director</p>
      <div class="contact__block">
        <p class="contact__label">Shop Address:</p>
        <p>12345, Address Goes Here<br>Country Name, 123456</p>
      </div>
      <div class="contact__block">
        <p class="contact__label">Mailing Address:</p>
        <p>12345, Address Goes Here<br>Country Name, 123456</p>
      </div>
      <p class="contact__line">
        <svg viewBox="0 0 24 24"><path fill="#fff" d="M6.6 10.8a15 15 0 0 0 6.6 6.6l2.2-2.2a1 1 0 0 1 1-.25 11.4 11.4 0 0 0 3.6.57 1 1 0 0 1 1 1V20a1 1 0 0 1-1 1A17 17 0 0 1 3 4a1 1 0 0 1 1-1h3.5a1 1 0 0 1 1 1c0 1.25.2 2.45.57 3.57a1 1 0 0 1-.25 1z"/></svg>
        (044)-555-0142
      </p>
      <p class="contact__line">
        <svg viewBox="0 0 24 24"><path fill="#fff" d="M2 5h20v14H2z"/><path fill="none" stroke="var(--brand-orange)" stroke-width="2" d="M2 5l10 8 10-8"/></svg>
        info@treadlinecivil.com
      </p>
    </div>
    <div class="back-brand">
      <div class="brand-dot"></div>
      <p class="brand-name">Tread Line<br>Civil Inc</p>
    </div>
  </section>
</main>
</body>
</html>
```